New Corporate Email footer (business card design) for 40th Anniversary for Timber Traders

We are traders in sustainable timber worldwide, specialising in tropical hardwoods.
We need to keep our current company logo, but update our email footer with a business card like design which marks the company's 40th Anniversary. 1981-2021. We would need:
Company Logo, Name and Address, website
Sender's: Name, Tel no, fax no, email address
We would need this in a format which we could update ourselves re names/phone numbers if any change.

Target Market(s)

Customers, suppliers, service providers

Contact Information for Business Card

Mavis Thorne
Tel: +44 (0) 208 473 2586
Fax: +44 (0) 208 473 5820
Email: mavis@pwlwoods.co.uk
Web: www.pwlwoods.co.uk

PWL Woods Ltd. 7 Falcon Court, Birchmore Way, Oakwick, Surrey CR4 6TJ, UNITED KINGDOM

IMPORTANT NOTICE - This message contains confidential information for the intended addressee only. Any views expressed are those of the sender not PWL Woods Ltd unless otherwise stated. If you receive this message [and any attachment(s)] in error you must not store, copy, disclose or otherwise use any part of it and should advise the sender immediately on 020 8473 9152. Internet communications are not guaranteed secure or virus free. PWL reserves the right to monitor all e-mail communications and does not accept responsibility for any loss or damage resulting from access of this e-mail or any file(s) attached.

Font styles to use
Sans Serif
Other font styles liked:
• not actually sure

Requirements
Must have
• mention of company's 40th Anniversary 1981-2021, which is the whole point of the design
Nice to have
• Our company colour is British Racing Green, but any green theme may be good
Maybe a tree design but allowing the company logo to stand out.

```html
<!DOCTYPE html>
<html lang="en">
<head>
<meta charset="utf-8">
<title>PWL Woods – Email Footer</title>
<link href="https://fonts.googleapis.com/css2?family=Lato:wght@400;700&display=swap" rel="stylesheet">
<style>
  :root {
    --backdrop: #dcdcdc;
    --card: #ffffff;
    --ink: #1e2a1f;
    --text: #222222;
    --rule: #b9b9b9;
    --notice: #7a3e12;
    --accent: #1b4d2e;
    --gold-light: #f3d27a;
    --gold-dark: #9c6b1c;
    --navy: #1c2533;
  }
  * { box-sizing: border-box; margin: 0; padding: 0; }
  html, body {
    width: 1200px; height: 756px; overflow: hidden;
    background: var(--backdrop);
    font-family: "Lato", sans-serif;
    color: var(--text);
  }
  .footer-card {
    position: absolute; left: 142px; top: 221px;
    width: 938px; height: 324px;
    background: var(--card);
    box-shadow: 2px 4px 6px rgba(0,0,0,.45);
  }
  .brand {
    position: absolute; left: 46px; top: 34px; width: 104px;
    display: flex; flex-direction: column; align-items: center; gap: 12px;
  }
  .brand-mark { width: 72px; height: 72px; background: var(--ink); border-radius: 50%; }
  .brand-name {
    font-weight: 700; font-size: 26px; line-height: 1.05; color: var(--ink);
    text-align: center;
  }
  .sender-name {
    position: absolute; left: 180px; top: 30px;
    font-weight: 700; font-size: 26px; color: var(--ink);
  }
  .rule { position: absolute; left: 178px; width: 593px; height: 2px; background: var(--rule); }
  .rule--top { top: 74px; }
  .rule--mid { top: 174px; }
  .rule--low { top: 215px; }
  .address {
    position: absolute; left: 178px; top: 84px;
    font-size: 20.5px; line-height: 26px; color: var(--text);
  }
  .contacts { position: absolute; left: 538px; top: 84px; list-style: none; }
  .contacts li {
    display: flex; align-items: center; gap: 9px;
    font-size: 20.5px; line-height: 26px;
  }
  .contacts svg { width: 19px; height: 19px; fill: var(--text); flex: none; }
  .social { position: absolute; left: 179px; top: 181px; display: flex; gap: 4px; }
  .social span { width: 23px; height: 23px; border-radius: 50%; background: var(--accent); }
  .website { position: absolute; left: 551px; top: 178px; font-size: 20.5px; }
  .anniversary-badge {
    position: absolute; left: 800px; top: 50px; width: 111px; height: 122px;
    border-radius: 8px 8px 50% 50% / 8px 8px 40% 40%;
    background: radial-gradient(circle at 50% 40%, var(--navy) 0 45%, var(--gold-dark) 60%, var(--gold-light) 100%);
  }
  .anniversary-years {
    position: absolute; left: 800px; top: 178px; width: 111px;
    text-align: center; font-size: 19.5px;
  }
  .notice {
    position: absolute; left: 40px; right: 40px; top: 232px;
    text-align: center; font-size: 14px; line-height: 17.5px; color: var(--notice);
  }
</style>
</head>
<body>
  <div class="footer-card">
    <div class="brand">
      <span class="brand-mark"></span>
      <span class="brand-name">PWL<br>Woods</span>
    </div>

    <h1 class="sender-name">Mavis Thorne</h1>
    <div class="rule rule--top"></div>

    <p class="address">PWL Woods Ltd. 7 Falcon Court,<br>Birchmore Way, Oakwick, Surrey<br>CR4 6TJ, UNITED KINGDOM</p>

    <ul class="contacts">
      <li>
        <svg viewBox="0 0 24 24" aria-hidden="true"><path d="M6.6 10.8c1.4 2.8 3.8 5.1 6.6 6.6l2.2-2.2c.3-.3.7-.4 1-.2 1.1.4 2.3.6 3.6.6.6 0 1 .4 1 1V20c0 .6-.4 1-1 1C10.6 21 3 13.4 3 4c0-.6.4-1 1-1h3.5c.6 0 1 .4 1 1 0 1.3.2 2.5.6 3.6.1.3 0 .7-.2 1z"/></svg>
        +44 (0) 208 473 2586
      </li>
      <li>
        <svg viewBox="0 0 24 24" aria-hidden="true"><path d="M7 3h10v4H7zM4 8h16a2 2 0 0 1 2 2v6h-4v5H6v-5H2v-6a2 2 0 0 1 2-2zm4 8v3h8v-3z"/></svg>
        +44 (0) 208 473 5820
      </li>
      <li>
        <svg viewBox="0 0 24 24" aria-hidden="true"><path d="M2 5h20v14H2zm2 2v.4l8 5.4 8-5.4V7z"/></svg>
        mavis@pwlwoods.co.uk
      </li>
    </ul>

    <div class="rule rule--mid"></div>
    <div class="social" aria-label="Social links"><span></span><span></span><span></span></div>
    <p class="website">www.pwlwoods.co.uk</p>
    <div class="rule rule--low"></div>

    <div class="anniversary-badge" role="img" aria-label="Gold 40th anniversary shield badge"></div>
    <p class="anniversary-years">1981-2021</p>

    <p class="notice">IMPORTANT NOTICE - This message contains confidential information for the intended addressee only. Any views expressed<br>are those of the sender not PWL Woods Ltd unless otherwise stated. If you receive this message [and any attachment(s)] in error<br>you must not store, copy, disclose or otherwise use any part of it and should advise the sender immediately on 020 8473 9152.<br>Internet communications are not guaranteed secure or virus free. PWL reserves the right to monitor all e-mail communications<br>and does not accept responsibility for any loss or damage resulting from access of this e-mail or any file(s) attached.</p>
  </div>
</body>
</html>
```